Moravel Aesthetic Doctor

I require an elegant, luxurious looking business card for my aesthetic business. I am a doctor and that will set me aside from competitors. I am planning to provide home and spa based treatments to clients with high expectations. I have attached my logo.

```html
<!DOCTYPE html>
<html lang="en">
<head>
<meta charset="utf-8">
<title>Moravel Aesthetic Doctor – Business Card</title>
<link href="https://fonts.googleapis.com/css2?family=Arimo:wght@400;700&display=swap" rel="stylesheet">
<style>
  :root {
    --stage: #222120;
    --paper: #ffffff;
    --ink-grey: #9a9ca1;
    --ink-soft: #7d7f84;
    --sky: #5bbde8;
    --ocean: #0e7ccf;
    --ocean-light: #52b9e8;
    --white: #ffffff;
    --dot-a: #5b7fc4;
    --dot-b: #c9648a;
  }
  * { box-sizing: border-box; margin: 0; padding: 0; }
  html, body {
    width: 1065px; height: 1200px; overflow: hidden;
    background: var(--stage);
    font-family: "Arimo", Arial, sans-serif;
  }
  .canvas { position: relative; width: 1065px; height: 1200px; }

  .card {
    position: absolute;
    width: 582px; height: 362px;
    box-shadow: 3px 4px 6px rgba(0,0,0,0.55);
  }

  /* Front */
  .card--front {
    left: 292px; top: 218px;
    background: var(--paper);
    border-radius: 0 181px 181px 0;
  }
  .holder { position: absolute; left: 30px; top: 46px; }
  .holder__name {
    font-size: 23px; font-weight: 700; color: var(--ink-grey);
    letter-spacing: -0.2px;
  }
  .holder__post { font-size: 15px; font-weight: 400; color: var(--sky); margin-left: 3px; }
  .holder__diploma {
    font-size: 17px; line-height: 21px; color: var(--sky); margin-top: 2px;
  }

  .brand {
    position: absolute; display: flex; align-items: center; gap: 12px;
  }
  .brand__mark {
    border-radius: 50%; flex: none;
  }
  .brand__name {
    font-weight: 400; text-transform: uppercase; line-height: 1;
  }
  .brand__name span { display: block; }

  .card--front .brand { left: 246px; top: 145px; }
  .card--front .brand__mark {
    width: 78px; height: 78px; border: 2px solid var(--ink-grey);
  }
  .card--front .brand__name { color: var(--ink-grey); font-size: 44px; letter-spacing: 2px; }
  .card--front .brand__name span + span { font-size: 18px; letter-spacing: 1.2px; margin-top: 6px; }

  .social { position: absolute; left: 29px; top: 219px; display: flex; gap: 4px; }
  .social__dot { width: 21px; height: 21px; border-radius: 50%; }
  .social__dot--a { background: var(--dot-a); }
  .social__dot--b { background: var(--dot-b); }

  .contact { position: absolute; left: 30px; top: 258px; list-style: none; }
  .contact li {
    display: flex; align-items: center; gap: 6px;
    font-size: 17.5px; color: var(--ink-soft); height: 22.5px;
  }
  .contact svg { width: 16px; height: 16px; flex: none; }

  /* Back */
  .card--back {
    left: 264px; top: 623px;
    border-radius: 181px 0 0 181px;
    background: linear-gradient(125deg,
      var(--ocean-light) 0%, var(--ocean-light) 22%,
      var(--ocean) 42%, var(--ocean-light) 58%,
      var(--ocean-light) 70%, var(--ocean) 88%, var(--ocean-light) 100%);
    color: var(--white);
    text-align: center;
  }
  .card--back .brand { left: 102px; top: 78px; }
  .card--back .brand__mark {
    width: 100px; height: 100px; border: 2px solid var(--white);
  }
  .card--back .brand__name { color: var(--white); font-size: 56px; letter-spacing: 2px; text-align: left; }
  .card--back .brand__name span + span { font-size: 23px; letter-spacing: 1.4px; margin-top: 8px; }

  .offer { position: absolute; left: 0; right: 0; top: 222px; }
  .offer__title { font-size: 17.5px; font-weight: 400; letter-spacing: 0.2px; }
  .offer__list { margin-top: 23px; font-size: 17.5px; line-height: 21.5px; }
  .offer__list .sep { display: inline-block; margin: 0 9px; font-size: 12px; vertical-align: 2px; }
</style>
</head>
<body>
<main class="canvas">

  <section class="card card--front" aria-label="Business card front">
    <div class="holder">
      <p class="holder__name">Dr Elsa Varenne<span class="holder__post">MRCPCH MD</span></p>
      <p class="holder__diploma">Australasian Diploma of<br>Aesthetic Medicine</p>
    </div>

    <div class="brand">
      <div class="brand__mark" aria-hidden="true"></div>
      <p class="brand__name"><span>Moravel</span><span>Aesthetic Doctor</span></p>
    </div>

    <div class="social" aria-label="Social media">
      <span class="social__dot social__dot--a"></span>
      <span class="social__dot social__dot--b"></span>
    </div>

    <ul class="contact">
      <li>
        <svg viewBox="0 0 16 16" aria-hidden="true"><path d="M4 1.5l2.3 3-1.4 1.6c.8 1.9 2.3 3.4 4.2 4.3l1.6-1.4 3 2.3-1.3 2.4c-5.3-.4-9.7-4.8-10.1-10.1z" fill="var(--sky)"/></svg>
        0800 555 014
      </li>
      <li>
        <svg viewBox="0 0 16 16" aria-hidden="true"><rect x="0.5" y="3" width="15" height="10" fill="var(--sky)"/><path d="M0.5 3l7.5 6 7.5-6" fill="none" stroke="#fff" stroke-width="1"/></svg>
        elsa@moravel.co.nz
      </li>
      <li>
        <svg viewBox="0 0 16 16" aria-hidden="true" fill="none" stroke="var(--sky)" stroke-width="1.2"><circle cx="8" cy="8" r="6.8"/><ellipse cx="8" cy="8" rx="3" ry="6.8"/><path d="M1.2 8h13.6M2.2 4.7h11.6M2.2 11.3h11.6"/></svg>
        www.moravel.co.nz
      </li>
    </ul>
  </section>

  <section class="card card--back" aria-label="Business card back">
    <div class="brand">
      <div class="brand__mark" aria-hidden="true"></div>
      <p class="brand__name"><span>Moravel</span><span>Aesthetic Doctor</span></p>
    </div>

    <div class="offer">
      <h2 class="offer__title">HOME AND SPA BASED TREATMENTS</h2>
      <p class="offer__list">
        Dermal injectables<span class="sep">●</span>Plasma facials<span class="sep">●</span>Microneedling<br>
        Skin boosters<span class="sep">●</span>Excessive sweating
      </p>
    </div>
  </section>

</main>
</body>
</html>
```